Power Generation Company needs a stationary design

We need a design for our letter envelope, A4 Envelope and letterhead. Our company name is BRIGHTVolt which i attached here sample our our call card. We are based in the Philippines and is into the Power Generation business. We own power facilities like Hydropower plant, Solar Power Plant, Diesel Power Plant, Gas Turbine Power Plant. We sell our power to various electric distribution companies, factories and office buildings.

Target Market(s)

Electric Distribution Companies and Factories

Industry/Entity Type

It Company

Colors
ec1f27

Requirements
Must have
• Logo and company name
Nice to have
• No specific
Should not have
• No specific

```html
<!DOCTYPE html>
<html lang="en">
<head>
<meta charset="utf-8">
<title>BRIGHTVolt Letterhead</title>
<link rel="stylesheet" href="https://fonts.googleapis.com/css2?family=Open+Sans:wght@400;600;700&display=swap">
<style>
  :root {
    --brand-red: #ec1f27;
    --brand-grey: #b9b9b9;
    --soft-grey: #dcdcdc;
    --ink: #4a4a4a;
    --paper: #ffffff;
    --backdrop: #e9a99e;
  }
  * { margin: 0; padding: 0; box-sizing: border-box; }
  html, body { width: 1200px; height: 784px; overflow: hidden; }
  body {
    background: var(--backdrop);
    font-family: "Open Sans", sans-serif;
    color: var(--ink);
    position: relative;
  }
  .letterhead {
    position: absolute;
    left: 338px; top: 22px;
    width: 523px; height: 740px;
    background: var(--paper);
    box-shadow: 0 6px 18px rgba(120, 50, 40, 0.25);
    overflow: hidden;
  }
  .edge-mark { position: absolute; width: 4px; }
  .edge-mark.left { left: 0; }
  .edge-mark.right { right: 0; }
  .edge-mark.red { background: var(--brand-red); }
  .edge-mark.grey { background: var(--brand-grey); }

  .brand {
    position: absolute; left: 26px; top: 22px;
  }
  .brand-name {
    display: flex; align-items: center; gap: 6px;
    font-size: 22px; font-weight: 600; color: var(--brand-red);
    line-height: 1;
  }
  .brand-dot {
    width: 12px; height: 12px; border-radius: 50%;
    background: var(--brand-red);
  }
  .brand-legal {
    margin-top: 5px;
    font-size: 9px; font-weight: 700; letter-spacing: 1.4px;
    color: #8a8a8a;
  }

  .services {
    position: absolute; right: 32px; top: 30px;
    list-style: none; text-align: right;
    font-size: 7.5px; line-height: 11px; color: var(--ink);
  }
  .services li::before {
    content: ""; display: inline-block;
    width: 0; height: 0; margin-right: 4px;
    border-left: 5px solid var(--brand-red);
    border-top: 3px solid transparent;
    border-bottom: 3px solid transparent;
  }

  .footer {
    position: absolute; left: 0; right: 0; bottom: 0; height: 110px;
  }
  .footer-rule {
    position: absolute; left: 30px; right: 30px; top: 18px;
    height: 1px; background: var(--soft-grey);
  }
  .contact-tab {
    position: absolute; left: 196px; top: 9px;
    width: 108px; height: 19px;
    background: var(--soft-grey);
    border-left: 3px solid var(--brand-red);
    border-right: 3px solid var(--brand-red);
    color: var(--brand-red);
    font-size: 8px; font-weight: 700;
    display: flex; align-items: center; justify-content: center;
  }
  .contact-address, .contact-row {
    position: absolute; left: 30px; right: 30px;
    font-size: 7.5px; color: var(--ink);
    display: flex; align-items: center; gap: 14px;
  }
  .contact-address { top: 36px; }
  .contact-row { top: 56px; justify-content: space-between; }
  .contact-item { display: flex; align-items: center; gap: 4px; white-space: nowrap; }
  .contact-icon { width: 8px; height: 8px; flex: none; }

  .footer-band {
    position: absolute; left: 0; right: 0; bottom: 0; height: 7px;
    display: flex;
  }
  .footer-band .seg-grey { background: var(--brand-grey); }
  .footer-band .seg-red { background: var(--brand-red); }
</style>
</head>
<body>
  <main class="letterhead">
    <span class="edge-mark left red" style="top:10px;height:20px"></span>
    <span class="edge-mark left grey" style="top:34px;height:18px"></span>
    <span class="edge-mark right red" style="top:14px;height:26px"></span>
    <span class="edge-mark right grey" style="top:46px;height:20px"></span>

    <header class="brand">
      <div class="brand-name"><span class="brand-dot"></span>BRIGHTVolt</div>
      <div class="brand-legal">BRIGHTVolt Power Inc.</div>
    </header>

    <ul class="services">
      <li>Hydropower Plant</li>
      <li>Solar Power Plant</li>
      <li>Diesel Power Plant</li>
      <li>Gas Turbine Power Plant</li>
    </ul>

    <footer class="footer">
      <div class="footer-rule"></div>
      <div class="contact-tab">Contact Detail</div>

      <div class="contact-address">
        <span class="contact-item">
          <svg class="contact-icon" viewBox="0 0 10 10"><circle cx="5" cy="5" r="5" fill="#ec1f27"/><path d="M5 2.2a1.9 1.9 0 0 0-1.9 1.9C3.1 5.5 5 7.8 5 7.8s1.9-2.3 1.9-3.7A1.9 1.9 0 0 0 5 2.2z" fill="#fff"/></svg>
          405 Harbor View Tower, 88 Palm Ave. Riverside Business Park, Sta. Rosa, Laguna City, 4026 Philippines
        </span>
      </div>

      <div class="contact-row">
        <span class="contact-item">
          <svg class="contact-icon" viewBox="0 0 10 10"><circle cx="5" cy="5" r="5" fill="#ec1f27"/><path d="M3 2.5l1.2 1.3-.6.8c.4.8 1 1.4 1.8 1.8l.8-.6 1.3 1.2-.8.9C4.6 7.7 2.3 5.4 2.1 3.3z" fill="#fff"/></svg>
          +632 555 0148
        </span>
        <span class="contact-item">
          <svg class="contact-icon" viewBox="0 0 10 10"><circle cx="5" cy="5" r="5" fill="#ec1f27"/><rect x="2.5" y="3" width="5" height="4" fill="#fff"/></svg>
          +632 555 0172
        </span>
        <span class="contact-item">
          <svg class="contact-icon" viewBox="0 0 10 10"><circle cx="5" cy="5" r="5" fill="#ec1f27"/><rect x="3.4" y="2" width="3.2" height="6" rx="0.6" fill="#fff"/></svg>
          +63 900 555 0193
        </span>
        <span class="contact-item">
          <svg class="contact-icon" viewBox="0 0 10 10"><circle cx="5" cy="5" r="5" fill="#ec1f27"/><rect x="2.3" y="3" width="5.4" height="4" fill="#fff"/><path d="M2.3 3L5 5.2 7.7 3" stroke="#ec1f27" stroke-width="0.6" fill="none"/></svg>
          info@brightvolt-power.com
        </span>
        <span class="contact-item">
          <svg class="contact-icon" viewBox="0 0 10 10"><circle cx="5" cy="5" r="5" fill="#ec1f27"/><circle cx="5" cy="5" r="2.7" stroke="#fff" stroke-width="0.6" fill="none"/><path d="M2.3 5h5.4M5 2.3v5.4" stroke="#fff" stroke-width="0.6"/></svg>
          www.brightvolt-power.com
        </span>
      </div>

      <div class="footer-band">
        <span class="seg-grey" style="width:26%"></span>
        <span class="seg-red" style="width:36%"></span>
        <span class="seg-grey" style="width:38%"></span>
      </div>
    </footer>
  </main>
</body>
</html>
```